Kestrel Row Club Ad creatives contest

I neednew ad banner for my site I can use to advertise on other adult sites our site is for Tradies and blue color workers to build their adult brands of themselves with videos streaming and market place and chat we have allt he things. I want to incorporate masculine men who are normal gay not all muscle thing like hairy dad bods who don't go to the gym every day t are still fit and healthly and not at over weight. It's for the normal guys who are working men. Im open to funny xxx, and a mix of nude and full on sex scenes. My clients maotly ahve a sense of humor and anything that's unique or makes people laugh or their brain want to click.. click bate all the way. This is for only men who like men so no hetero or females please. Here is some of the stuff we have had previously. Remember it's technically a porn site so please use nudes mainly I'm I dont. Have pictures to supply sorry. But think lumberjack masculine dad's body working men. Muscle is ok but not like Adonis model think what your bf looks like or if your a dude prolly your body.
Target Market(s)
Gay, bisexual and straight men who like blue- collar men and porn.
Industry/Entity Type
Adult entertainment
Requirements
Must have
- Partial nudity if not.full nude.. website logo and "kestrel row club" somewhere

Nice to have
- Nudes of masculine men, and half naked regular adverage men ok n

Should not have
- Women or heterosexual references

```html
<!DOCTYPE html>
<html lang="en">
<head>
<meta charset="utf-8">
<title>Kestrel Row Club – Ad Banners</title>
<link href="https://fonts.googleapis.com/css2?family=Oswald:wght@600;700&family=Work+Sans:wght@400&family=Bowlby+One&display=swap" rel="stylesheet">
<style>
  :root {
    --violet: #6d1a98;
    --magenta: #c31e9a;
    --indigo: #6a5bc8;
    --sun: #fdbd00;
    --sun-deep: #f0a800;
    --grape: #6a43a0;
    --gold-text: #d99a1a;
    --ink: #1f1400;
    --logo-brown: #3b230c;
    --white: #ffffff;
  }
  * { box-sizing: border-box; margin: 0; padding: 0; }
  html, body { width: 1038px; height: 1200px; overflow: hidden; background: var(--white); }
  .canvas { position: relative; width: 1038px; height: 1200px; }

  .banner { position: absolute; left: 20px; width: 997px; height: 570px; overflow: hidden; }

  /* ---------- Banner one ---------- */
  .banner--neon {
    top: 18px;
    background:
      radial-gradient(ellipse 260px 340px at 330px 130px, var(--magenta) 0%, rgba(195,30,154,0) 100%),
      radial-gradient(ellipse 300px 260px at 900px 430px, var(--indigo) 0%, rgba(106,91,200,0) 100%),
      radial-gradient(ellipse 220px 200px at 80px 470px, #a5229e 0%, rgba(165,34,158,0) 100%),
      var(--violet);
  }
  .banner--neon .brand {
    position: absolute; left: 96px; top: 58px;
    display: flex; align-items: center; gap: 10px;
  }
  .brand-dot { width: 34px; height: 34px; border-radius: 50%; background: var(--sun); }
  .banner--neon .brand-name {
    font-family: "Oswald", sans-serif; font-weight: 600; font-size: 22px;
    color: var(--white); letter-spacing: 0.5px;
  }
  .neon-headline {
    position: absolute; left: 113px; top: 228px;
    font-family: "Oswald", sans-serif; font-weight: 700; font-size: 56px;
    line-height: 79px; color: var(--white);
    text-shadow: 3px 3px 0 var(--sun-deep);
  }
  .neon-copy {
    position: absolute; left: 114px; top: 388px; width: 380px;
    font-family: "Work Sans", sans-serif; font-size: 12.5px; line-height: 21px;
    color: var(--white);
  }
  .cta {
    position: absolute; left: 113px; top: 453px; width: 112px; height: 40px;
    border-radius: 20px; background: var(--sun);
    font-family: "Oswald", sans-serif; font-weight: 600; font-size: 13px;
    color: var(--ink); display: flex; align-items: center; justify-content: center;
  }
  .neon-photo {
    position: absolute; left: 510px; top: 0; width: 487px; height: 570px;
    background: radial-gradient(ellipse 170px 260px at 250px 320px, #e7799e 0%, #c94f8f 55%, rgba(109,26,152,0) 100%);
  }

  /* ---------- Banner two ---------- */
  .banner--angled { top: 611px; background: var(--white); box-shadow: 0 4px 14px rgba(0,0,0,0.12); }
  .angled-shapes { position: absolute; inset: 0; width: 997px; height: 570px; }
  .banner--angled .brand {
    position: absolute; left: 740px; top: 170px;
    display: flex; align-items: center; gap: 10px;
  }
  .banner--angled .brand-dot { background: var(--grape); width: 30px; height: 30px; }
  .banner--angled .brand-name {
    font-family: "Bowlby One", sans-serif; font-size: 19px; color: var(--grape);
  }
  .angled-headline {
    position: absolute; right: 98px; top: 318px; text-align: right;
    font-family: "Bowlby One", sans-serif; font-size: 36px; line-height: 72px;
    color: var(--grape);
  }
  .angled-headline .accent { color: var(--gold-text); }
</style>
</head>
<body>
<main class="canvas">

  <section class="banner banner--neon">
    <div class="neon-photo" role="img" aria-label="Photo of a shirtless man in red shorts posing with a hand on his neck"></div>
    <div class="brand">
      <span class="brand-dot"></span>
      <span class="brand-name">Kestrel Row Club</span>
    </div>
    <h1 class="neon-headline">Workin Hard? or<br>Hardly Working?</h1>
    <p class="neon-copy">Lorem ipsum dolor sit amet, consectetur adipiscing elit, sed do eiusmod tempor incididunt ut labore et dolore magna aliqua.</p>
    <a class="cta">Get Started</a>
  </section>

  <section class="banner banner--angled">
    <svg class="angled-shapes" viewBox="0 0 1400 800" preserveAspectRatio="none" aria-hidden="true">
      <defs>
        <linearGradient id="photoTone" x1="0" y1="0" x2="1" y2="1">
          <stop offset="0" stop-color="#c9ad7c"/>
          <stop offset="0.5" stop-color="#d7a784"/>
          <stop offset="1" stop-color="#b89866"/>
        </linearGradient>
      </defs>
      <polygon points="0,0 990,0 955,35 0,35" fill="var(--sun)"/>
      <polygon points="960,0 1400,0 1400,35 930,35" fill="var(--grape)"/>
      <polygon points="1080,35 1175,35 395,800 305,800" fill="var(--grape)"/>
      <polygon points="1400,495 1235,660 1400,800" fill="var(--sun)"/>
      <polygon points="1300,690 1170,800 1400,800" fill="var(--sun-deep)"/>
      <polygon points="940,800 980,757 1230,757 1190,800" fill="var(--grape)"/>
    </svg>
    <svg class="angled-shapes" viewBox="0 0 1400 800" preserveAspectRatio="none" role="img" aria-label="Photo of a shirtless man with hands behind his head against a weathered wall">
      <polygon points="0,35 1080,35 305,800 0,800" fill="url(#photoTone)"/>
      <polygon points="0,0 280,0 0,275" fill="var(--sun)"/>
    </svg>
    <div class="brand">
      <span class="brand-dot"></span>
      <span class="brand-name">Kestrel Row Club</span>
    </div>
    <h2 class="angled-headline">Workin <span class="accent">Hard? or</span><br>Hardly <span class="accent">Working?</span></h2>
  </section>

</main>
</body>
</html>
```